a business advisory consulting website

I need a website 3-5 pages to sell my professional services in IT and Project management Consulting. My company name is Crestline Advisory Consulting. I want it to be device friendly and easy to navigate for the busy executive however intriguing enough.
I have attached some info I drafted on About the company and personal Bio. Also there is a website that I really like that I have attached the initial site pdf and websites that I like are here: https://tollmeradvisors.example, https://quarvelanalytics.example, https://www.dorvikstudylearning.example as examples. Thanks
Updates

Hi Designers, I have uploaded the logo in 3D .png format, to assist in the web design.

Target Market(s)

B2B, governments, IT companies, Project Management companies and Consulting firms, small medium enterprises to large corporate enterprises.

Industry/Entity Type

It Professional

Coding

Coded - Design and coding required

Number of Pages Required

5+ page

Font styles to use
Sans Serif

Requirements
Must have
• Home, About company, the team, what we do and contact us
Nice to have
• Blog
Should not have
• pop ups, flash

```html
<!DOCTYPE html>
<html lang="en">
<head>
<meta charset="utf-8">
<title>Crestline Advisory Consulting</title>
<link href="https://fonts.googleapis.com/css2?family=Poppins:ital,wght@0,400;0,500;0,600;1,400&family=Oswald:wght@600&family=Open+Sans:wght@300&display=swap" rel="stylesheet">
<style>
:root{
  --navy:#1d2340;
  --navy-deep:#151a30;
  --red:#e42527;
  --red-soft:#e8393b;
  --ink:#1f2544;
  --text:#6b6f7d;
  --pale:#eef3f5;
  --white:#ffffff;
}
*{margin:0;padding:0;box-sizing:border-box}
html,body{width:1200px;height:3812px;overflow:hidden}
body{font-family:'Poppins',sans-serif;color:var(--ink);background:var(--white);position:relative}
.abs{position:absolute}
section,header,footer{position:absolute;left:0;width:1200px;overflow:hidden}
.red{color:var(--red)}
.explore{font-size:12px;font-weight:600;color:var(--red);display:flex;align-items:center;gap:6px}
.explore svg{width:13px;height:13px}

/* header & hero */
.hero{top:0;height:713px;background:linear-gradient(100deg,#252c4c 0%,#1d2340 55%,#2a3150 100%)}
.hero-photo{left:577px;top:133px;width:415px;height:580px;background:radial-gradient(ellipse at 50% 30%,#6a5a52 0%,#3b3f55 45%,#22283f 80%);border-radius:200px 200px 0 0}
.brand{left:163px;top:26px;display:flex;align-items:center;gap:10px}
.brand-mark{width:30px;height:30px;background:var(--red)}
.brand-name{font-weight:600;font-size:17px;line-height:18px;color:var(--white);text-transform:uppercase}
.nav{left:522px;top:39px;display:flex;gap:22px;font-size:11px;color:var(--white);letter-spacing:.2px}
.nav .active{color:var(--red);position:relative}
.nav .active:after{content:"";position:absolute;left:0;right:0;bottom:-8px;height:2px;background:var(--red)}
.search{left:938px;top:39px;width:14px;height:14px}
.burger{left:1010px;top:39px;width:29px}
.burger i{display:block;height:2px;background:var(--red);margin-bottom:5px}
.burger i:nth-child(2){margin-left:7px}
.hero-kicker{left:161px;top:232px;font-family:'Open Sans',sans-serif;font-weight:300;font-size:37px;color:var(--red)}
.hero-title{left:161px;top:282px;font-family:'Oswald',sans-serif;font-weight:600;font-size:48px;line-height:53px;color:var(--white);text-transform:uppercase;letter-spacing:.5px}
.hero-text{left:161px;top:398px;width:340px;font-size:14.5px;line-height:22px;color:#dfe2ec}
.btn{background:var(--red);color:var(--white);font-weight:600;font-size:14px;border-radius:22px;display:flex;align-items:center;justify-content:center;text-transform:uppercase}
.hero-btn{left:161px;top:457px;width:150px;height:44px}

/* welcome */
.welcome{top:713px;height:449px}
.welcome-kicker{left:262px;top:72px;font-size:15px;font-weight:500}
.welcome-title{left:260px;top:100px;font-size:37px;font-weight:500;line-height:41px;text-transform:uppercase}
.welcome-rule{left:525px;top:105px;width:1px;height:163px;background:#dcdde3}
.welcome-copy{left:585px;top:122px;width:350px;font-size:11.6px;line-height:18px;color:var(--text)}
.welcome-copy p{margin-bottom:16px}
.welcome-copy p.dark{color:var(--ink)}
.welcome .explore{left:586px;top:361px}

/* services */
.services{top:1162px;height:614px;background:var(--pale)}
.section-title{width:1200px;text-align:center;font-size:37px;font-weight:500;text-transform:uppercase}
.section-sub{width:1200px;text-align:center;font-size:12px;line-height:21px;color:var(--text)}
.services .section-title{top:70px}
.services .section-sub{top:127px}
.card{top:198px;width:203px;height:339px;background:var(--white)}
.card-img{left:0;top:0;width:192px;height:150px}
.card h3{left:30px;top:170px;font-size:13.5px;font-weight:500;line-height:18px;width:160px}
.card p{left:30px;top:236px;width:160px;font-size:10.5px;line-height:18px;color:var(--text)}
.card .explore{left:29px;top:302px}
.card.featured{background:var(--red)}
.card.featured .card-img{left:-12px;top:-13px}
.card.featured h3,.card.featured p,.card.featured .explore{color:var(--white)}
.card.featured h3{top:157px;left:18px}
.card.featured p{left:16px;top:236px}
.card.featured .explore{left:17px}
.card:not(.featured) .card-img{left:-12px;top:-13px}
.card:not(.featured) h3,.card:not(.featured) p,.card:not(.featured) .explore{left:18px}

/* bio */
.bio{top:1776px;height:580px}
.bio-title{left:220px;top:122px;font-size:34px;font-weight:500;line-height:41px;text-transform:uppercase}
.bio-copy{left:218px;top:224px;width:300px;font-size:11.6px;line-height:21px;color:var(--text)}
.bio-copy p{margin-bottom:10px}
.bio-copy em{color:var(--ink);font-weight:500}
.bio-btn{left:217px;top:464px;width:202px;height:40px;font-size:13px}
.bio-square{left:615px;top:263px;width:74px;height:74px;background:var(--red)}
.bio-dot{left:928px;top:400px;width:66px;height:66px;border-radius:50%;background:var(--red)}
.bio-photo{left:628px;top:91px;width:340px;height:489px;background:linear-gradient(180deg,#cfc3b9 0%,#3b4a78 35%,#1f2a52 100%);border-radius:150px 150px 0 0}

/* banner */
.banner{top:2356px;height:226px;background:linear-gradient(90deg,#3c3636 0%,#2a2f48 45%,#1d2340 100%)}
.banner-text{top:56px;width:1200px;text-align:center;font-size:21px;font-weight:500;line-height:32px;color:var(--white)}
.banner-phone{top:133px;width:1200px;text-align:center;font-size:24px;font-weight:500;color:var(--red)}

/* blog */
.blog{top:2582px;height:577px}
.blog .section-title{top:68px}
.blog .section-sub{top:124px}
.post{top:200px;width:240px;height:310px}
.post-img{left:0;top:0;width:240px;height:192px}
.post-date{left:20px;top:183px;background:var(--red);color:var(--white);font-size:11.5px;border-radius:4px;padding:5px 14px}
.post-date-wrap{left:12px;top:178px;width:228px;height:14px;background:var(--white)}
.post h3{left:22px;top:237px;width:210px;font-size:13.3px;font-weight:500;line-height:21px}
.post .explore{left:22px;top:288px}

/* contact */
.contact{top:3159px;height:563px;background:linear-gradient(180deg,#e23236 0%,#e84448 100%)}
.contact-panel{left:0;top:132px;width:562px;height:314px;background:var(--navy)}
.contact-title{left:212px;top:50px;font-size:30px;font-weight:500;color:var(--white);text-transform:uppercase}
.contact-row{left:212px;display:flex;align-items:flex-start;gap:16px;color:var(--white)}
.ci{width:34px;height:34px;border-radius:50%;border:1.5px solid var(--red);display:flex;align-items:center;justify-content:center;flex:none}
.ci svg{width:15px;height:15px}
.contact-row.addr{top:110px}
.contact-row.addr div{font-size:10.5px;line-height:16px;margin-top:0}
.contact-row.addr b{font-weight:600;display:block;margin-bottom:3px}
.contact-row.tel{top:195px;align-items:center;font-size:15px;font-weight:500}
.contact-row.mail{top:240px;align-items:center;font-size:11.5px}
.form-head{left:655px;top:100px;width:308px;text-align:center;font-size:17px;line-height:27px;color:var(--white);letter-spacing:.3px}
.field{left:655px;width:308px;height:36px;background:var(--white);font-size:10px;color:#9b9ea8;padding:11px 16px}
.field.msg{height:70px}
.submit{left:753px;top:443px;width:104px;height:41px;border:1.5px solid var(--white);border-radius:22px;color:var(--white);font-size:13px;font-weight:600;display:flex;align-items:center;justify-content:center}

/* footer */
.footer{top:3722px;height:90px;background:var(--navy)}
.copy{left:163px;top:38px;font-size:10.5px;color:#c9ccd8}
.footer .brand{left:535px;top:28px}
.socials{left:950px;top:37px;display:flex;gap:16px}
.socials span{width:17px;height:17px;border-radius:50%;border:1.5px solid var(--white)}
.socials span:first-child{border-color:var(--red)}
</style>
</head>
<body>

<header class="hero">
  <div class="abs hero-photo" role="img" aria-label="Portrait of a smiling consultant in a suit with arms crossed, over a dimmed office background"></div>
  <div class="abs brand"><span class="brand-mark"></span><span class="brand-name">Crestline<br>Advisory</span></div>
  <nav class="abs nav">
    <span class="active">HOME</span><span>ABOUT COMPANY</span><span>TEAM</span><span>WHAT WE DO</span><span>CONTACT US</span>
  </nav>
  <svg class="abs search" viewBox="0 0 14 14" fill="none" stroke="#fff" stroke-width="1.6"><circle cx="5.5" cy="5.5" r="4.3"/><path d="M8.8 8.8 13 13"/></svg>
  <div class="abs burger"><i></i><i></i><i></i></div>
  <p class="abs hero-kicker">We Are Expert In</p>
  <h1 class="abs hero-title">Project Management<br>IT and Consulting</h1>
  <p class="abs hero-text">We help you scale your business operations to become highly profitable.</p>
  <a class="abs btn hero-btn">Get Started</a>
</header>

<section class="welcome">
  <p class="abs welcome-kicker">Welcome To</p>
  <h2 class="abs welcome-title">Crestline<br><span class="red">Advisory</span></h2>
  <div class="abs welcome-rule"></div>
  <div class="abs welcome-copy">
    <p>We are a specialist operational excellence firm, delivering consulting and advisory services in six core capabilities, across all industries and all business lines to improve perfor -mance, efficiency, profitability, automation and scalability, for clients across Australia.</p>
    <p>We're known for our pragmatism, in depth analysis, strategic insight &amp; nurturing longterm client self sufficiency.</p>
    <p class="dark">We approach business consulting differently, with a Genuine Client Partnership model that builds client capability and rightsized solutions for the client.</p>
  </div>
  <a class="abs explore">Explore More <svg viewBox="0 0 14 14" fill="none" stroke="currentColor" stroke-width="1.5"><path d="M1 7h11M8 3l4 4-4 4"/><circle cx="7" cy="7" r="6" stroke-dasharray="0"/></svg></a>
</section>

<section class="services">
  <h2 class="abs section-title">What <span class="red">We Do</span></h2>
  <p class="abs section-sub">We offer first-class, Strategic and Financial insights that help you simplify and<br>structure your processes to become a lean Efficient Enterprise.</p>

  <article class="abs card featured" style="left:173px">
    <div class="abs card-img" role="img" aria-label="Hand holding a phone over a stock chart" style="background:linear-gradient(135deg,#0e1d36,#3d5676)"></div>
    <h3 class="abs">Market Entry</h3>
    <p class="abs">Lorem ipsum is simply text of the printing and typesetting industry Lorem ipsum.</p>
    <a class="abs explore">Explore More <svg viewBox="0 0 14 14" fill="none" stroke="currentColor" stroke-width="1.5"><path d="M1 7h11M8 3l4 4-4 4"/></svg></a>
  </article>
  <article class="abs card" style="left:398px">
    <div class="abs card-img" role="img" aria-label="Digital healthcare icons on a blue screen" style="background:linear-gradient(135deg,#0a2a4a,#1f6a9a)"></div>
    <h3 class="abs">Technology Ananlysis within healthcare</h3>
    <p class="abs">Lorem ipsum is simply text of the printing and typesetting industry Lorem ipsum.</p>
    <a class="abs explore">Explore More <svg viewBox="0 0 14 14" fill="none" stroke="currentColor" stroke-width="1.5"><path d="M1 7h11M8 3l4 4-4 4"/></svg></a>
  </article>
  <article class="abs card" style="left:623px">
    <div class="abs card-img" role="img" aria-label="Domed government building under a blue sky" style="background:linear-gradient(180deg,#2e5bb0,#8aa6c8 60%,#4a5a3a)"></div>
    <h3 class="abs">Process Improvement within government</h3>
    <p class="abs">Lorem ipsum is simply text of the printing and typesetting industry Lorem ipsum.</p>
    <a class="abs explore">Explore More <svg viewBox="0 0 14 14" fill="none" stroke="currentColor" stroke-width="1.5"><path d="M1 7h11M8 3l4 4-4 4"/></svg></a>
  </article>
  <article class="abs card" style="left:848px">
    <div class="abs card-img" role="img" aria-label="Two people reviewing documents at a desk" style="background:linear-gradient(135deg,#4a4c55,#8c8a88)"></div>
    <h3 class="abs">Advise for early stage startup</h3>
    <p class="abs">Lorem ipsum is simply text of the printing and typesetting industry Lorem ipsum.</p>
    <a class="abs explore">Explore More <svg viewBox="0 0 14 14" fill="none" stroke="currentColor" stroke-width="1.5"><path d="M1 7h11M8 3l4 4-4 4"/></svg></a>
  </article>
</section>

<section class="bio">
  <h2 class="abs bio-title">Daniel<br><span class="red">Okwara Bio</span></h2>
  <div class="abs bio-copy">
    <p>Daniel Okwara is an IT professional with more than 20 years of experience turning business initiatives into technology solutions.</p>
    <p>His expertise has been identifying deficiencies and developing or facilitating the best solutions for an outcome that is satisfactory to all stakeholders involved.</p>
    <p><em>Daniel improves business processes as older organizations restructure or migrate to newer technologies.</em></p>
  </div>
  <a class="abs btn bio-btn">More About Daniel</a>
  <div class="abs bio-square"></div>
  <div class="abs bio-dot"></div>
  <div class="abs bio-photo" role="img" aria-label="Portrait of the consultant standing in a navy suit"></div>
</section>

<section class="banner" role="img" aria-label="Smiling professional in a dimmed background photo">
  <p class="abs banner-text">We help You Scale your Business Operations<br>to Become Highly Profitable.</p>
  <p class="abs banner-phone">+(1) 555 014 2290</p>
</section>

<section class="blog">
  <h2 class="abs section-title">Latest <span class="red">Blog</span></h2>
  <p class="abs section-sub">Lorem Ipsum is simply text of the printing nturies, but also the leap<br>into electronic typesetting remaining.</p>

  <article class="abs post" style="left:217px">
    <div class="abs post-img" role="img" aria-label="Team meeting in a bright office" style="background:linear-gradient(135deg,#b9c2cc,#5d6673)"></div>
    <div class="abs post-date-wrap"></div>
    <span class="abs post-date">12 aug 2020</span>
    <h3 class="abs">Lorem Ipsum is simply text of the printing nturies</h3>
    <a class="abs explore">Explore More <svg viewBox="0 0 14 14" fill="none" stroke="currentColor" stroke-width="1.5"><path d="M1 7h11M8 3l4 4-4 4"/></svg></a>
  </article>
  <article class="abs post" style="left:479px">
    <div class="abs post-img" role="img" aria-label="Colleagues gathered around a standing table" style="background:linear-gradient(135deg,#e6eef2,#8fa3b0)"></div>
    <div class="abs post-date-wrap"></div>
    <span class="abs post-date">12 aug 2020</span>
    <h3 class="abs">Lorem Ipsum is simply text of the printing nturies</h3>
    <a class="abs explore">Explore More <svg viewBox="0 0 14 14" fill="none" stroke="currentColor" stroke-width="1.5"><path d="M1 7h11M8 3l4 4-4 4"/></svg></a>
  </article>
  <article class="abs post" style="left:741px">
    <div class="abs post-img" role="img" aria-label="Business people working at a laptop" style="background:linear-gradient(135deg,#9fb0bf,#3a4556)"></div>
    <div class="abs post-date-wrap"></div>
    <span class="abs post-date">12 aug 2020</span>
    <h3 class="abs">Lorem Ipsum is simply text of the printing nturies</h3>
    <a class="abs explore">Explore More <svg viewBox="0 0 14 14" fill="none" stroke="currentColor" stroke-width="1.5"><path d="M1 7h11M8 3l4 4-4 4"/></svg></a>
  </article>
</section>

<section class="contact" role="img" aria-label="City skyline in red tint">
  <div class="abs contact-panel"></div>
  <div class="abs" style="left:0;top:132px">
    <h2 class="abs contact-title" style="white-space:nowrap">Contact <span class="red">Info</span></h2>
    <div class="abs contact-row addr">
      <span class="ci"><svg viewBox="0 0 16 16" fill="none" stroke="#e42527" stroke-width="1.4"><path d="M8 15s5-5 5-8.5A5 5 0 0 0 3 6.5C3 10 8 15 8 15z"/><circle cx="8" cy="6.5" r="1.8"/></svg></span>
      <div style="width:200px;white-space:normal"><b>Crestline Advisory Consulting</b>101 - Lorem ipsum simple text print type text industry.</div>
    </div>
    <div class="abs contact-row tel" style="white-space:nowrap">
      <span class="ci"><svg viewBox="0 0 16 16" fill="none" stroke="#e42527" stroke-width="1.4"><path d="M4 2h2.5l1 3-1.7 1.2a8 8 0 0 0 4 4L11 8.5l3 1V12a2 2 0 0 1-2 2A10 10 0 0 1 2 4a2 2 0 0 1 2-2z"/></svg></span>
      +(1) 555 014 2290
    </div>
    <div class="abs contact-row mail" style="white-space:nowrap">
      <span class="ci"><svg viewBox="0 0 16 16" fill="none" stroke="#e42527" stroke-width="1.4"><rect x="2" y="4" width="12" height="9" rx="1"/><path d="m2 5 6 4 6-4"/></svg></span>
      info@crestlineadvisory.example
    </div>
  </div>
  <p class="abs form-head">Have an Any Question Please<br>Contact Us Today !</p>
  <div class="abs field" style="top:177px">Your Name *</div>
  <div class="abs field" style="top:222px">Organization *</div>
  <div class="abs field" style="top:267px">Phone *</div>
  <div class="abs field" style="top:312px">Email *</div>
  <div class="abs field msg" style="top:357px">Write us a Message *</div>
  <a class="abs submit">SUBMIT</a>
</section>

<footer class="footer">
  <p class="abs copy">©<span class="red">Crestline Advisory Consulting</span> - 2020 All rights reserved.</p>
  <div class="abs brand"><span class="brand-mark"></span><span class="brand-name">Crestline<br>Advisory</span></div>
  <div class="abs socials"><span></span><span></span><span></span></div>
</footer>

</body>
</html>
```